Retail Jewelry Business Card Design Project

We are in need of a new business card design for a retail jewelry store. This store is in the business of fine jewelry including but not specific to bridal jewelry, diamonds, designer jewelry and watches.

This store has been in business for 20 years but continues to strive for a modern professional appeal. The main colors use for this business are a royal blue, white and silver.

Target Market(s)

Target market is ages 18-50

Industry/Entity Type

Jewelry

Requirements
Must have
• Sales Person Name
Sales Person Email Address

Store Address
Store Phone
Website

Standard business card size. No odd shapes or sizes.
Nice to have
• Overall modern feel for card.

We have thought that a design with a nice feature of the logo on the back of the card would be nice but open to ideas.
Should not have
• No specific images of jewelry should be used.

```html
<!DOCTYPE html>
<html lang="en">
<head>
<meta charset="utf-8">
<title>Marlowe Reid Fine Jewelry – Business Cards</title>
<link href="https://fonts.googleapis.com/css2?family=Open+Sans:wght@400;600;700&display=swap" rel="stylesheet">
<style>
  :root {
    --page-bg: #ffffff;
    --royal: #2e3192;
    --lavender: #7169b5;
    --night: #0b0f1c;
    --night-glow: #16203a;
    --ink: #333333;
    --rule: #555555;
    --white: #ffffff;
    --shadow: rgba(0, 0, 0, 0.35);
  }
  * { box-sizing: border-box; margin: 0; padding: 0; }
  html, body {
    width: 1200px; height: 1000px; overflow: hidden;
    background: var(--page-bg);
    font-family: "Open Sans", Arial, sans-serif;
  }
  .canvas { position: relative; width: 1200px; height: 1000px; }

  .card {
    position: absolute; left: 285px; width: 653px;
    border-radius: 22px; overflow: hidden;
    box-shadow: 3px 5px 7px var(--shadow);
  }

  /* Front */
  .card--front {
    top: 104px; height: 374px;
    background: radial-gradient(ellipse at 65% 30%, var(--night-glow) 0%, var(--night) 70%);
  }
  .front-brand {
    position: absolute; left: 36px; top: 222px;
    color: var(--white); font-weight: 600;
    font-size: 40px; line-height: 1.1;
  }
  .front-brand .brand-sub {
    display: block; font-size: 17px; letter-spacing: 3px; margin-top: 10px;
  }
  .front-url {
    position: absolute; left: 54px; top: 325px;
    color: var(--white); font-size: 15px; letter-spacing: 1.2px;
  }

  /* Back */
  .card--back {
    top: 534px; height: 376px;
    background: var(--white);
  }
  .back-brand {
    position: absolute; left: 0; right: 0; top: 56px;
    text-align: center; color: var(--royal); font-weight: 600;
    font-size: 52px; line-height: 1.1;
  }
  .back-brand .brand-sub {
    display: block; font-size: 22px; letter-spacing: 4px; margin-top: 14px;
  }
  .person {
    position: absolute; right: 363px; top: 249px; text-align: right;
  }
  .person-name { font-size: 20px; font-weight: 700; color: var(--royal); }
  .person-name .surname { color: var(--lavender); }
  .person-title { font-size: 16px; color: var(--ink); margin-top: 2px; }

  .divider {
    position: absolute; left: 326px; top: 211px;
    width: 1px; height: 123px; background: var(--rule);
  }

  .contact {
    position: absolute; left: 362px; top: 215px;
    font-size: 16px; color: var(--ink); line-height: 22px;
  }
  .contact-address { margin-bottom: 4px; }
  .contact-line { display: flex; align-items: center; gap: 9px; }
  .contact-line svg { width: 16px; height: 14px; flex: none; fill: var(--lavender); }

  .footer-band {
    position: absolute; left: 0; right: 0; bottom: 0; height: 23px;
    background: linear-gradient(90deg, var(--royal) 0 32px, var(--night) 32px,
      var(--night-glow) 50%, var(--night) calc(100% - 32px), var(--royal) calc(100% - 32px));
  }
</style>
</head>
<body>
<main class="canvas">
  <section class="card card--front" aria-label="Card front">
    <div class="front-brand">Marlowe Reid<span class="brand-sub">FINE JEWELRY</span></div>
    <p class="front-url">www.marlowereidjewelry.com</p>
  </section>

  <section class="card card--back" aria-label="Card back">
    <div class="back-brand">Marlowe Reid<span class="brand-sub">FINE JEWELRY</span></div>

    <div class="person">
      <p class="person-name">Marlowe Reid <span class="surname">Halvorsen</span></p>
      <p class="person-title">Owner</p>
    </div>

    <div class="divider"></div>

    <div class="contact">
      <p class="contact-address">2210 Larkspur Avenue<br>Bayview, FL 32499</p>
      <p class="contact-line">
        <svg viewBox="0 0 16 14" aria-hidden="true"><path d="M1 5c0-3 14-3 14 0v1h-4V4.5H5V6H1z"/><path d="M4 7h8l2 6H2z"/></svg>
        000.000.0000
      </p>
      <p class="contact-line">
        <svg viewBox="0 0 16 14" aria-hidden="true"><path d="M1 2h14v10H1z M2 3l6 5 6-5" stroke="#fff" stroke-width="1"/></svg>
        marlowe@marlowereidjewelry.com
      </p>
      <p class="contact-line">
        <svg viewBox="0 0 16 14" aria-hidden="true"><circle cx="8" cy="7" r="6.5"/><path d="M1.5 7h13M8 .5v13M3 3.5h10M3 10.5h10" stroke="#fff" stroke-width="0.9" fill="none"/><ellipse cx="8" cy="7" rx="3" ry="6.5" stroke="#fff" stroke-width="0.9" fill="none"/></svg>
        www.marlowereidjewelry.com
      </p>
    </div>

    <div class="footer-band"></div>
  </section>
</main>
</body>
</html>
```